Professional, Attractive, Simple Website Needed!!

We completed the design for our logo.

We need a website built out around this.

Here are a couple samples of how we want ours formatted.

http://brimvoltco.com

http://www.ravelbeam.com/lp/free-quote?LeadSource=Search%20Engine&ProgramName=searchads&experience=qual&language=en&type=brd&gclid=Xk7PLmqwTRZBNVuEYcaHdFgWsLoPeRtQnMxVbCzJaKiOuYtReWqAsDfGhJkLzXcVbNmQwErTyUiOpAsDfGhJkLzX_wcB

http://quorel.co
Updates

Project Deadline Extended
Reason: Extending this deadline due to our delay in providing designers with content for each page. This is coming in next 24 hours.

Project Deadline Extended
Reason: Due to scheduling conflicts and extended travel delays related to Puerto Rico, the deadline has been extended. Your patience is greatly appreciated.

Project Deadline Extended
Reason: Travel and scheduling conflicts have made it impossible to give this project the thorough review it deserves, therefore I am extending the deadline. Thank you for your patience!

Target Market(s)

Home Owners who earn 60k + household annually

Industry/Entity Type

It Professional

Coding

Coded - Design and coding required

Number of Pages Required

5+ page

Font styles to use
Serif

Colors
34a7d8
9bcb3c

Requirements
Must have
• Simple
• Lead form Entry (Ability for visitor to enter Name, number and address for a quote)
• Sleek Design
• Professional
• Testimonials
• Use color Scheme of Design Logo Attached
Nice to have
• Video when site starts
• Like this
• https://www.vidplexa.com/watch?v=Qm8rTbLw3Np&feature=vidplexa.be
Should not have
• Should not include Commercial solar
• Should not include wind power

```html
<!DOCTYPE html>
<html lang="en">
<head>
<meta charset="utf-8">
<title>Sunward Home Energy</title>
<link rel="stylesheet" href="https://fonts.googleapis.com/css2?family=Open+Sans:ital,wght@0,400;0,600;0,700;1,400&display=swap">
<style>
:root{
  --green:#8dc63f;
  --green-dark:#7ab232;
  --blue:#1589cf;
  --blue-deep:#0f78b8;
  --grey-bg:#efefef;
  --dark:#232323;
  --text:#333;
  --muted:#666;
  --white:#fff;
}
*{box-sizing:border-box;margin:0;padding:0}
html,body{width:1200px;height:3309px;overflow:hidden}
body{position:relative;font-family:"Open Sans",Arial,sans-serif;color:var(--text);background:var(--white)}
.abs{position:absolute}
.backdrop{position:absolute;left:0;top:0}
.center{text-align:center;left:0;width:1200px}

/* header */
.logo{left:88px;top:30px;display:flex;align-items:center;gap:10px}
.logo-mark{width:40px;height:40px;border-radius:50%;background:var(--blue)}
.logo-name{color:var(--white);font-size:17px;font-weight:600;line-height:1.1;width:110px}
.nav{left:440px;top:50px;display:flex;gap:34px;align-items:center;font-size:16px;color:var(--white)}
.nav .active{color:var(--green)}
.login{background:var(--green);color:var(--white);border-radius:18px;padding:5px 24px;font-size:16px}
.social{display:flex;gap:10px}
.social span{width:24px;height:24px;border-radius:50%;background:var(--white);display:block}
.nav-rule{left:88px;top:115px;width:1024px;height:1px;background:rgba(255,255,255,.45)}

/* hero */
.play{left:568px;top:254px;width:64px;height:64px;border-radius:50%;background:rgba(20,20,20,.75);border:3px solid rgba(255,255,255,.8)}
.hero-title{top:352px;font-size:52px;color:var(--white);font-weight:400}
.hero-sub{top:423px;font-size:24px;color:var(--white)}
.dots{left:568px;top:598px;display:flex;gap:8px}
.dots span{width:8px;height:8px;border-radius:50%;background:var(--white)}
.dots .on{background:var(--green)}

/* services */
.section-title{font-size:36px;font-weight:400}
.services-title{top:712px;color:var(--white)}
.service{width:300px;text-align:center;color:var(--white)}
.service-icon{width:116px;height:116px;margin:0 auto;border-radius:50%;border:4px solid var(--white);display:flex;align-items:center;justify-content:center}
.service-icon span{width:96px;height:96px;border-radius:50%;background:var(--white);display:flex;align-items:center;justify-content:center}
.service h3{font-size:22px;font-weight:400;margin-top:26px}
.service p{font-size:13.5px;line-height:22px;margin-top:10px}

/* about */
.about-back{left:152px;top:1212px;width:100px;height:300px;background:var(--blue)}
.about-photo{left:161px;top:1224px;width:353px;height:292px;background:linear-gradient(180deg,#9ec6e6 0%,#7fa56a 45%,#3f6b9c 70%,#2b4f80 100%);box-shadow:0 10px 22px rgba(0,0,0,.3)}
.about-title{left:565px;top:1244px;font-size:32px;color:#222}
.about-copy{left:565px;top:1300px;width:506px;font-size:13.5px;line-height:23px;color:var(--muted)}
.btn-small{background:var(--green);color:var(--white);border-radius:16px;font-size:13px;font-weight:600;padding:5px 20px}
.about-btn{left:565px;top:1468px}

/* what we do */
.what-title{top:1700px;color:#222}
.card{top:1796px;width:312px;height:289px;background:var(--white);box-shadow:0 2px 6px rgba(0,0,0,.18);text-align:center}
.card-photo{height:165px}
.card h4{font-size:17px;font-weight:400;margin-top:20px;color:#222}
.card p{font-size:12.5px;line-height:20px;color:var(--muted);margin:8px 20px 0}
.card a{display:block;font-size:12px;color:var(--blue);margin-top:4px;text-decoration:none}

/* testimonials */
.test-title{top:2264px;color:#222}
.quote{left:260px;top:2348px;width:680px;text-align:center;font-size:16px;line-height:28px;color:#555}
.quote b{color:var(--blue);font-size:22px}
.avatar{left:554px;top:2438px;width:92px;height:92px;border-radius:50%;background:linear-gradient(#c9ccd2,#7f8a99);border:3px solid #ddd}
.arrow{top:2468px;width:16px;height:30px}
.author{top:2548px;font-size:15px;font-style:italic;color:#444}

/* contact */
.contact-title{top:2712px;color:var(--white)}
.field{top:2808px;width:289px;height:58px;background:var(--white);border-radius:3px;font-size:16px;color:#444;padding:17px 16px}
.submit{left:518px;top:2894px;width:166px;height:42px;border-radius:21px;background:var(--green);color:var(--white);font-size:22px;text-align:center;line-height:42px}

/* footer */
.foot-head{top:3062px;font-size:16px;color:var(--white)}
.foot-list{font-size:12.5px;color:var(--white);line-height:30px}
.foot-list li{list-style:none;display:flex;align-items:center;gap:8px}
.news{left:794px;top:3060px;width:260px;color:var(--white);font-size:13px;line-height:19px}
.news .social span{width:24px}
.news-form{display:flex;margin-top:10px}
.news-form div{width:194px;height:30px;background:var(--white);font-size:12px;color:#888;padding:7px 10px}
.news-form span{width:60px;height:30px;background:var(--blue);font-size:12px;line-height:30px;text-align:center}
.foot-rule{left:88px;top:3216px;width:1024px;height:1px;background:rgba(255,255,255,.15)}
.copyright{top:3252px;font-size:12px;color:var(--white)}
</style>
</head>
<body>

<svg class="backdrop" width="1200" height="3309" viewBox="0 0 1200 3309">
  <rect x="0" y="2930" width="1200" height="379" fill="#232323"/>
  <path d="M0 2600 Q600 2760 1200 2600 L1200 2956 Q600 3070 0 2956 Z" fill="#1589cf"/>
  <path d="M0 1577 Q600 1710 1200 1577 L1200 2228 Q600 2120 0 2228 Z" fill="#efefef"/>
  <path d="M0 560 L1200 560 L1200 1170 Q600 1010 0 1170 Z" fill="#8dc63f"/>
  <path d="M0 0 L1200 0 L1200 596 Q600 730 0 596 Z" fill="url(#heroGrad)" role="img" aria-label="Photo of a house roof covered with solar panels under a blue sky"/>
  <defs>
    <linearGradient id="heroGrad" x1="0" y1="0" x2="0" y2="1">
      <stop offset="0" stop-color="#2f5c93"/>
      <stop offset=".35" stop-color="#5a7ea8"/>
      <stop offset=".65" stop-color="#34465e"/>
      <stop offset="1" stop-color="#5c5750"/>
    </linearGradient>
  </defs>
</svg>

<header>
  <div class="abs logo"><span class="logo-mark"></span><span class="logo-name">Sunward Home Energy</span></div>
  <nav class="abs nav">
    <span class="active">Home</span><span>Services</span><span>Products</span><span>About Us</span><span>Contact Us</span>
    <span class="login">Login</span>
    <span class="social"><span></span><span></span></span>
  </nav>
  <div class="abs nav-rule"></div>
</header>

<section class="hero">
  <div class="abs play">
    <svg width="58" height="58" viewBox="0 0 58 58"><path d="M23 18 L40 29 L23 40 Z" fill="#fff"/></svg>
  </div>
  <h1 class="abs center hero-title">Sunward Home Energy</h1>
  <p class="abs center hero-sub">Neque porro quisquam est qui dolorem</p>
  <div class="abs dots"><span class="on"></span><span></span><span></span><span></span><span></span></div>
</section>

<section class="services">
  <h2 class="abs center section-title services-title">Our Services</h2>
  <div class="abs service" style="left:128px;top:807px">
    <div class="service-icon"><span><svg width="48" height="40" viewBox="0 0 48 40"><rect x="4" y="4" width="40" height="24" fill="var(--green)"/><path d="M4 12H44M4 20H44M17 4V28M31 4V28" stroke="#fff" stroke-width="2"/><rect x="22" y="28" width="4" height="8" fill="var(--green)"/><rect x="14" y="35" width="20" height="3" fill="var(--green)"/></svg></span></div>
    <h3>Quisquam</h3>
    <p>It has survived not only five centuries,<br>but also the leap into electronic</p>
  </div>
  <div class="abs service" style="left:448px;top:807px">
    <div class="service-icon"><span><svg width="44" height="44" viewBox="0 0 44 44"><circle cx="22" cy="22" r="12" fill="none" stroke="var(--green)" stroke-width="4"/><path d="M22 2V8M22 36V42M2 22H8M36 22H42M8 8L12 12M32 32L36 36M36 8L32 12M8 36L12 32" stroke="var(--green)" stroke-width="3"/></svg></span></div>
    <h3>Dolorem</h3>
    <p>It has survived not only five centuries,<br>but also the leap into electronic</p>
  </div>
  <div class="abs service" style="left:788px;top:807px">
    <div class="service-icon"><span><svg width="48" height="44" viewBox="0 0 48 44"><circle cx="24" cy="8" r="5" fill="var(--green)"/><path d="M10 20 L38 20 L44 40 L4 40 Z" fill="var(--green)"/><path d="M7 30H41M18 20L15 40M30 20L33 40" stroke="#fff" stroke-width="2"/></svg></span></div>
    <h3>Consectetur</h3>
    <p>It has survived not only five centuries,<br>but also the leap into electronic</p>
  </div>
</section>

<section class="about">
  <div class="abs about-back"></div>
  <div class="abs about-photo" role="img" aria-label="Photo of solar panels in front of city towers and trees"></div>
  <h2 class="abs about-title">About Sunward Home Energy</h2>
  <p class="abs about-copy">It is a long established fact that a reader will be distracted by the readable content of a page when looking at its layout. The point of using Lorem Ipsum is that it has a more-or-less normal distribution of letters, as opposed to using 'Content here, content here', making it look like readable English. Many desktop publishing packages and web page editors now use Lorem Ipsum as their default model text, and a search for 'lorem ipsum' will uncover many web sites still in their infancy.</p>
  <span class="abs btn-small about-btn">Read More</span>
</section>

<section class="what">
  <h2 class="abs center section-title what-title">What We Do</h2>
  <article class="abs card" style="left:95px">
    <div class="card-photo" role="img" aria-label="Photo of a tiled house roof with solar panels" style="background:linear-gradient(180deg,#a9cdea,#2d4f86 55%,#a4553a)"></div>
    <h4>Porro quisquam</h4>
    <p>It has survived not only five centuries, but also the leap into electronic typesetting,</p>
    <a>Read More »</a>
  </article>
  <article class="abs card" style="left:435px">
    <div class="card-photo" role="img" aria-label="Photo of an installer working on rooftop solar panels" style="background:linear-gradient(180deg,#9cc0de,#3a5f95 50%,#26416e)"></div>
    <h4>Dolorem ipsum</h4>
    <p>It has survived not only five centuries, but also the leap into electronic typesetting,</p>
    <a>Read More »</a>
  </article>
  <article class="abs card" style="left:772px">
    <div class="card-photo" role="img" aria-label="Photo of solar panel rows at sunrise" style="background:linear-gradient(180deg,#e8eef4,#b9cfe2 45%,#5f7fa6)"></div>
    <h4>Porro quisquam</h4>
    <p>It has survived not only five centuries, but also the leap into electronic typesetting,</p>
    <a>Read More »</a>
  </article>
</section>

<section class="testimonials">
  <h2 class="abs center section-title test-title">Testimonials</h2>
  <p class="abs quote"><b>“</b> It is a long established fact that a reader will be distracted by the readable content of a page when looking at its layout. The point of using Lorem Ipsum is that it has a more-or-less normal distribution of letters, as opposed to using 'Content here, content here' <b>”</b></p>
  <svg class="abs arrow" style="left:510px" viewBox="0 0 16 30"><path d="M13 3 L3 15 L13 27" fill="none" stroke="#888" stroke-width="2.5"/></svg>
  <div class="abs avatar" role="img" aria-label="Customer portrait"></div>
  <svg class="abs arrow" style="left:674px" viewBox="0 0 16 30"><path d="M3 3 L13 15 L3 27" fill="none" stroke="#888" stroke-width="2.5"/></svg>
  <p class="abs center author">Dana Whitfield</p>
</section>

<section class="quick-contact">
  <h2 class="abs center section-title contact-title">Quick Contact</h2>
  <div class="abs field" style="left:159px">Name</div>
  <div class="abs field" style="left:468px">Number</div>
  <div class="abs field" style="left:777px">Address</div>
  <div class="abs submit">Submit</div>
</section>

<footer>
  <h5 class="abs foot-head" style="left:161px">Contact</h5>
  <ul class="abs foot-list" style="left:161px;top:3092px">
    <li><svg width="10" height="13" viewBox="0 0 10 13"><path d="M5 0A5 5 0 0 1 10 5C10 8 5 13 5 13S0 8 0 5A5 5 0 0 1 5 0Z" fill="#fff"/><circle cx="5" cy="5" r="2" fill="#232323"/></svg>412 W Linden Ct, Maplebrook, IL 60412</li>
    <li><svg width="11" height="11" viewBox="0 0 11 11"><path d="M2 0L4 3L3 4.5C4 6.5 4.5 7 6.5 8L8 7L11 9L9.5 11C4 10.5 0.5 7 0 1.5Z" fill="#fff"/></svg>(555) 014-2790</li>
    <li><svg width="12" height="9" viewBox="0 0 12 9"><rect width="12" height="9" fill="#fff"/><path d="M0 0L6 5L12 0" fill="none" stroke="#232323"/></svg>hello@sunwardhome.example</li>
  </ul>
  <h5 class="abs foot-head" style="left:545px">Information</h5>
  <ul class="abs foot-list" style="left:545px;top:3092px;line-height:24px;font-size:11.5px">
    <li>» Privacy Policy</li><li>» Login</li><li>» Advanced Search</li><li>» Contact Us</li>
  </ul>
  <div class="abs news">
    <div class="social"><span></span><span></span></div>
    <p style="margin-top:12px">Neque porro quisquam est qui dolorem quia dolor sit amet, consectetur</p>
    <div class="news-form"><div>Email address</div><span>Submit</span></div>
  </div>
  <div class="abs foot-rule"></div>
  <p class="abs center copyright">Copyright © 2017 All Rights Reserved</p>
</footer>

</body>
</html>
```